Design for Chatterly Ad to promote Laptops purchase

Need a graphic design for a Chatterly Ad - to promote 2 laptops (PC and Lumetra) with the stated required ad-text.

AD TEXT:

FOR SME BUSINESS ONLY!
Chat with us!
To get advice on how to apply
and defray up to 80%* of business laptop purchase cost!

*Terms and Conditions apply

Image for reference only

Target Market(s)

Small medium business

Font styles to use
Sans Serif

Requirements
Must have
• 2 laptop images (see attached ) - 1 vector image of LUMETRA , and pls try to create another vector image of PC laptop (where screen is showing Blue Petalix screen)

```html
<!DOCTYPE html>
<html lang="en">
<head>
<meta charset="utf-8">
<title>Chatterly – SME Business Laptop Ad</title>
<link rel="stylesheet" href="https://fonts.googleapis.com/css2?family=Poppins:wght@400;500;600&display=swap">
<style>
  :root {
    --light-bg: #f4f4f4;
    --light-ink: #1f1d1e;
    --dark-bg: #1c1c1c;
    --dark-ink: #ffffff;
    --gap-bg: #ffffff;
    --lumetra-tone-a: #c46bbf;
    --lumetra-tone-b: #5b3a8f;
    --petalix-tone-a: #1a7cf0;
    --petalix-tone-b: #0a1f9a;
    --silver: #c9c9cc;
  }
  * { margin: 0; padding: 0; box-sizing: border-box; }
  html, body {
    width: 1124px;
    height: 1200px;
    overflow: hidden;
    background: var(--gap-bg);
    font-family: "Poppins", sans-serif;
  }
  .ad {
    position: absolute;
    left: 0;
    width: 1124px;
    height: 589px;
    background: var(--light-bg);
    color: var(--light-ink);
  }
  .ad--light { top: 0; }
  .ad--dark { top: 611px; background: var(--dark-bg); color: var(--dark-ink); }

  .laptop {
    position: absolute;
  }
  .laptop--lumetra {
    left: 147px; top: 96px; width: 384px; height: 207px;
    background: linear-gradient(135deg, var(--lumetra-tone-b) 0%, var(--lumetra-tone-a) 45%, var(--lumetra-tone-b) 80%, var(--silver) 100%);
    border-radius: 10px 10px 14px 14px;
  }
  .laptop--petalix {
    left: 597px; top: 96px; width: 348px; height: 222px;
    background: linear-gradient(160deg, var(--petalix-tone-b) 0%, var(--petalix-tone-a) 55%, var(--silver) 78%, #e6e6e8 100%);
    border-radius: 8px 8px 16px 16px;
  }

  .headline {
    position: absolute;
    left: 0; right: 0;
    text-align: center;
    font-weight: 500;
    letter-spacing: -0.5px;
    line-height: 1;
  }
  .headline--main { top: 356px; font-size: 44px; }
  .headline--sub  { top: 416px; font-size: 37px; }

  .offer {
    position: absolute;
    left: 0; right: 0; top: 466px;
    text-align: center;
    font-size: 27.5px;
    font-weight: 400;
    line-height: 32px;
  }
  .offer strong { font-weight: 600; }

  .footnote {
    position: absolute;
    left: 34px; top: 559px;
    font-size: 12px;
    font-weight: 400;
  }
</style>
</head>
<body>

  <section class="ad ad--light">
    <div class="laptop laptop--lumetra" role="img" aria-label="Illustration of an open Lumetra laptop with a pink and purple galaxy wallpaper"></div>
    <div class="laptop laptop--petalix" role="img" aria-label="Illustration of an open silver PC laptop showing the blue Petalix desktop screen"></div>
    <h1 class="headline headline--main">For SME Business only!</h1>
    <h2 class="headline headline--sub">Chat with us!</h2>
    <p class="offer">To get advice on how to apply<br>and defray <strong>up to 80%</strong>* business laptop purchase cost!</p>
    <p class="footnote">*Terms and conditions apply</p>
  </section>

  <section class="ad ad--dark">
    <div class="laptop laptop--lumetra" role="img" aria-label="Illustration of an open Lumetra laptop with a pink and purple galaxy wallpaper"></div>
    <div class="laptop laptop--petalix" role="img" aria-label="Illustration of an open silver PC laptop showing the blue Petalix desktop screen"></div>
    <h1 class="headline headline--main">For SME Business only!</h1>
    <h2 class="headline headline--sub">Chat with us!</h2>
    <p class="offer">To get advice on how to apply<br>and defray <strong>up to 80%</strong>* business laptop purchase cost!</p>
    <p class="footnote">*Terms and conditions apply</p>
  </section>

</body>
</html>
```